Brightwater Care Partners, LLC Business Card update!

would like a classier business card. Our cards currently just have our logo and contact information. Need better use of color and creativity
Logo attached.

Target Market(s)

Potential clients, contacts, existing clients. We are a consulting company

Industry/Entity Type

Business

Contact Information for Business Card

We like our colors but just have a boring card with our logo and a white background. I want something that stands out.

Colors
ec1f27
757575

Requirements
Must have
• Color to stay consistent. Logo provided
Nice to have
• Just better use of color/ design

```html
<!DOCTYPE html>
<html lang="en">
<head>
<meta charset="utf-8">
<title>Brightwater Care Partners – Business Card</title>
<link href="https://fonts.googleapis.com/css2?family=Open+Sans:wght@400;600;700&display=swap" rel="stylesheet">
<style>
  :root {
    --brand-red: #c1272d;
    --accent-red: #ec1f27;
    --brand-grey: #757575;
    --card-black: #050505;
    --stage: #1b1b1b;
    --white: #ffffff;
    --text-light: #e8e8e8;
  }
  html, body {
    margin: 0;
    width: 1200px;
    height: 900px;
    overflow: hidden;
    background: var(--stage);
    font-family: "Open Sans", Arial, sans-serif;
  }
  .canvas {
    position: relative;
    width: 1200px;
    height: 900px;
  }
  .business-card {
    position: absolute;
    left: 180px;
    top: 210px;
    width: 840px;
    height: 480px;
    display: flex;
    box-shadow: 0 20px 50px rgba(0,0,0,0.6);
  }
  .brand-panel {
    width: 410px;
    background: var(--brand-red);
    display: flex;
    flex-direction: column;
    align-items: center;
    justify-content: center;
    gap: 22px;
  }
  .brand-mark-circle {
    width: 70px;
    height: 70px;
    border-radius: 50%;
    background: var(--white);
  }
  .brand-panel-name {
    color: var(--white);
    font-weight: 600;
    font-size: 34px;
    line-height: 1.2;
    text-align: center;
    margin: 0;
  }
  .contact-panel {
    flex: 1;
    background: var(--card-black);
    padding: 56px 40px 0 46px;
    box-sizing: border-box;
  }
  .company-name {
    color: var(--accent-red);
    font-weight: 400;
    font-size: 30px;
    line-height: 1.1;
    margin: 0 0 70px;
    text-align: right;
  }
  .person-name {
    color: var(--white);
    font-weight: 700;
    font-size: 23px;
    margin: 0;
  }
  .person-title {
    color: var(--accent-red);
    font-size: 17px;
    margin: 2px 0 26px;
  }
  .contact-list {
    list-style: none;
    margin: 0;
    padding: 0;
  }
  .contact-item {
    display: flex;
    align-items: flex-start;
    gap: 14px;
    color: var(--text-light);
    font-size: 17px;
    line-height: 27px;
  }
  .contact-icon {
    flex: none;
    width: 13px;
    height: 13px;
    margin-top: 7px;
    fill: var(--accent-red);
  }
</style>
</head>
<body>
<main class="canvas">
  <article class="business-card">
    <section class="brand-panel">
      <div class="brand-mark-circle"></div>
      <p class="brand-panel-name">Brightwater<br>Care Partners</p>
    </section>
    <section class="contact-panel">
      <h1 class="company-name">Brightwater Care Partners</h1>
      <h2 class="person-name">Owner Name</h2>
      <p class="person-title">Managing Director</p>
      <ul class="contact-list">
        <li class="contact-item">
          <svg class="contact-icon" viewBox="0 0 16 16"><path d="M1 5c0-2 1-3 7-3s7 1 7 3v2h-4V5H5v2H1z"/><rect x="3" y="8" width="10" height="7" rx="1"/></svg>
          <span>000 123 456 456</span>
        </li>
        <li class="contact-item">
          <svg class="contact-icon" viewBox="0 0 16 16"><rect x="0" y="3" width="16" height="11" rx="1"/><path d="M1 4l7 5 7-5" stroke="#050505" stroke-width="1.5" fill="none"/></svg>
          <span>iinfo@compnayname.com</span>
        </li>
        <li class="contact-item">
          <svg class="contact-icon" viewBox="0 0 16 16"><path d="M6 10l4-4" stroke="#ec1f27" stroke-width="2"/><path d="M7 4l2-2a3 3 0 014 4l-2 2M9 12l-2 2a3 3 0 01-4-4l2-2" stroke="#ec1f27" stroke-width="2" fill="none"/></svg>
          <span>www.companyname.com</span>
        </li>
        <li class="contact-item">
          <svg class="contact-icon" viewBox="0 0 16 16"><path d="M8 0a5.5 5.5 0 00-5.5 5.5C2.5 10 8 16 8 16s5.5-6 5.5-10.5A5.5 5.5 0 008 0zm0 8a2.5 2.5 0 110-5 2.5 2.5 0 010 5z"/></svg>
          <span>Address line1, Address Line,<br>Country, 012</span>
        </li>
      </ul>
    </section>
  </article>
</main>
</body>
</html>
```